Quillbrook IT company focused on 3 areas of IT

Looking for something similar to attached cards. Logo for quillbrook also attached.. Looking for something clean as far as colors (surprise me).. Quill stands for 3 primary areas, web design, consulting and network infrastructure design. Please email me if you have any questions. Looking forward to seeing how creative and professional this card will look. Thank you,

Target Market(s)

Small business/consumers looking for It services

Industry/Entity Type

It Service

Contact Information for Business Card

Dorin Vasek
Principal Consultant

202-555-0173

www.quillbrook-example.com
dvasek@quillbrook-example.com

27416 Copper Lantern Way,
Germantown, MD 20999

Colors

Designer to choose colors to be used in the design.

Requirements
Must have
• attached Logo design. Feel free to play with the colors.. If you have a better idea for a card, please fee free to send me. Looking for something clean/modern. Should have tech feel, not cheesy.
Nice to have
• Surprise me :-)..

```html
<!DOCTYPE html>
<html lang="en">
<head>
<meta charset="utf-8">
<title>Quillbrook — Business Card</title>
<link rel="stylesheet" href="https://fonts.googleapis.com/css2?family=Work+Sans:wght@400;500;600&display=swap">
<style>
  :root {
    --backdrop: #2a2a2c;
    --card: #1d1d1f;
    --card-edge: #262628;
    --accent: #29a9e1;
    --ink: #f2f2f2;
    --rule: #e8e8e8;
  }
  * { margin: 0; padding: 0; box-sizing: border-box; }
  html, body {
    width: 1200px; height: 900px; overflow: hidden;
    background: var(--backdrop);
    font-family: "Work Sans", Arial, sans-serif;
  }
  .stage {
    width: 1200px; height: 900px;
    display: flex; flex-direction: column; align-items: center; justify-content: center;
    gap: 40px;
  }
  .card {
    width: 660px; height: 377px;
    background: var(--card);
    border: 1px solid var(--card-edge);
    position: relative;
  }
  .card-back .pattern-area {
    position: absolute; inset: 0;
    background: linear-gradient(135deg, #1b1b1d 0%, #242426 60%, #2c2c2e 100%);
  }
  .card-front { display: flex; align-items: center; }
  .brand {
    width: 300px; display: flex; align-items: center; justify-content: center; gap: 12px;
  }
  .brand-mark { width: 18px; height: 18px; background: var(--accent); }
  .brand-name {
    font-weight: 600; font-size: 34px; color: var(--accent); letter-spacing: 0.5px;
  }
  .divider { width: 2px; height: 170px; background: var(--rule); }
  .contact { padding-left: 48px; color: var(--ink); }
  .person-name {
    font-weight: 500; font-size: 30px; color: var(--accent);
    text-transform: uppercase; letter-spacing: 1px; line-height: 1;
  }
  .person-title { font-size: 17px; margin-top: 4px; letter-spacing: 0.5px; }
  .address { font-size: 16px; margin-top: 16px; line-height: 1.35; letter-spacing: 0.5px; }
  .lines { list-style: none; margin-top: 12px; font-size: 16px; letter-spacing: 0.4px; }
  .lines li { display: flex; align-items: center; gap: 10px; line-height: 1.5; }
  .lines svg { width: 12px; height: 12px; flex: none; }
</style>
</head>
<body>
<main class="stage">
  <section class="card card-back" aria-label="Card back">
    <div class="pattern-area" role="img" aria-label="Repeating embossed brand pattern on dark card stock"></div>
  </section>

  <section class="card card-front" aria-label="Card front">
    <div class="brand">
      <span class="brand-mark"></span>
      <span class="brand-name">Quillbrook</span>
    </div>
    <div class="divider"></div>
    <div class="contact">
      <h1 class="person-name">Dorin Vasek</h1>
      <p class="person-title">Principal Consultant</p>
      <p class="address">27416 Copper Lantern Way,<br>Germantown, MD 20999</p>
      <ul class="lines">
        <li>
          <svg viewBox="0 0 12 12" aria-hidden="true"><path d="M3 1 L5 3.5 L4 5 Q5 7 7 8 L8.5 7 L11 9 L9.5 11 Q5 11 1 3 Z" fill="var(--accent)"/></svg>
          202-555-0173
        </li>
        <li>
          <svg viewBox="0 0 12 12" aria-hidden="true"><rect x="1" y="2.5" width="10" height="7" fill="none" stroke="var(--accent)" stroke-width="1.3"/><path d="M1 2.5 L6 6.5 L11 2.5" fill="none" stroke="var(--accent)" stroke-width="1.3"/></svg>
          dvasek@quillbrook-example.com
        </li>
        <li>
          <svg viewBox="0 0 12 12" aria-hidden="true"><circle cx="6" cy="6" r="5" fill="none" stroke="var(--accent)" stroke-width="1.1"/><ellipse cx="6" cy="6" rx="2.2" ry="5" fill="none" stroke="var(--accent)" stroke-width="1"/><path d="M1 6 H11" stroke="var(--accent)" stroke-width="1"/></svg>
          www.quillbrook-example.com
        </li>
      </ul>
    </div>
  </section>
</main>
</body>
</html>
```